Logo, Web and Mobile Designs for enterprise social media platform

All the details are in the attached document, please start reading the scope document first which explains what is this project about and the details about the needed deliverables, after that please read the UI_Requirements document which will detail what is expected regarding the coded web version since this is a coded contest, it is very important that you meet the UI requirements or suggest something else but we will need to agree first before working on the coded version

Good Luck

Target Market(s)

Enterprise Social Media

Industry/Entity Type

Media

Coding

Coded - Design and coding required

Number of Pages Required

5+ page

Font styles to use
Sans Serif

Requirements
Must have
• All the must haves are listed in the scope document so please check before you start

```html
<!DOCTYPE html>
<html lang="en">
<head>
<meta charset="utf-8">
<title>Teamvora — Sign Up</title>
<link rel="stylesheet" href="https://fonts.googleapis.com/css2?family=Lato:wght@400;700&display=swap">
<style>
  :root {
    --brand-blue: #00a2f3;
    --header-dark: #1f262e;
    --footer-dark: #20272e;
    --ink: #1f2328;
    --muted: #6b6f74;
    --field-border: #c9ccd0;
    --white: #ffffff;
    --photo-light: #eef4f8;
    --photo-mid: #c7d3e2;
    --photo-deep: #7c8aa5;
    --social-grey: #8a949e;
  }
  * { box-sizing: border-box; margin: 0; padding: 0; }
  html, body { width: 1200px; height: 713px; overflow: hidden; }
  body { font-family: "Lato", sans-serif; color: var(--ink); background: var(--white); position: relative; }

  .site-header { position: absolute; left: 0; top: 0; width: 1200px; height: 79px; background: var(--header-dark); }
  .brand { position: absolute; left: 0; top: 0; width: 316px; height: 79px; background: var(--brand-blue);
    color: var(--white); font-weight: 700; font-size: 25px; line-height: 79px; padding-left: 33px; letter-spacing: .3px; }
  .login-label { position: absolute; color: var(--white); font-size: 16px; }
  .login-label.email { left: 601px; top: 20px; }
  .login-label.password { left: 843px; top: 24px; }
  .login-input { position: absolute; top: 20px; width: 158px; height: 28px; background: var(--white); border: 0; border-radius: 2px; }
  .login-input.email { left: 657px; }
  .login-input.password { left: 925px; }
  .login-button { position: absolute; left: 1097px; top: 19px; width: 73px; height: 27px; background: var(--brand-blue);
    color: var(--white); font-size: 15px; text-align: center; line-height: 27px; }
  .login-note { position: absolute; top: 56px; color: var(--white); font-size: 11px; font-weight: 700; display: flex; align-items: center; gap: 8px; }
  .login-note.keep { left: 657px; }
  .login-note.forgot { left: 929px; }

  .hero { position: absolute; left: 0; top: 79px; width: 1200px; height: 595px; background: var(--white); }
  .hero-photo { position: absolute; left: 0; top: 0; width: 895px; height: 595px;
    background: linear-gradient(100deg, var(--photo-light) 0%, var(--photo-mid) 30%, var(--photo-deep) 48%, var(--photo-mid) 65%, var(--photo-light) 88%, var(--white) 100%); }

  .signup { position: absolute; left: 697px; top: 48px; width: 480px; height: 530px; }
  .signup-title { font-size: 25px; font-weight: 700; line-height: 1; }
  .signup-tagline { font-size: 13px; font-weight: 700; margin-top: 6px; }
  .field { position: absolute; height: 39px; background: var(--white); border: 1px solid var(--field-border); border-radius: 2px;
    font-size: 14px; font-weight: 700; color: #4a4e53; padding-left: 13px; line-height: 37px; }
  .field.first { left: 0; top: 79px; width: 231px; }
  .field.last { left: 247px; top: 79px; width: 231px; }
  .field.wide { left: 0; width: 478px; }
  .field.email { top: 141px; }
  .field.email-again { top: 204px; }
  .field.password { top: 266px; }
  .birthday-label { position: absolute; left: 0; top: 327px; font-size: 19px; font-weight: 700; line-height: 23px; }
  .select { position: absolute; top: 368px; width: 98px; height: 39px; background: var(--white); border: 1px solid var(--field-border);
    border-radius: 2px; font-size: 14px; font-weight: 700; color: #4a4e53; padding-left: 12px; line-height: 37px; }
  .select.day { left: -2px; }
  .select.month { left: 112px; }
  .select.year { left: 226px; }
  .select svg { position: absolute; right: 14px; top: 16px; }
  .terms { position: absolute; left: 2px; top: 424px; width: 460px; font-size: 12px; line-height: 18px; color: var(--muted); }
  .signup-button { position: absolute; left: 0; top: 478px; width: 101px; height: 43px; background: var(--brand-blue);
    color: var(--white); font-size: 14px; font-weight: 700; text-align: center; line-height: 43px; }

  .site-footer { position: absolute; left: 0; top: 674px; width: 1200px; height: 39px; background: var(--footer-dark); }
  .copyright { position: absolute; left: 15px; top: 0; line-height: 39px; color: var(--white); font-size: 12px; }
  .social { position: absolute; right: 23px; top: 8px; display: flex; gap: 4px; list-style: none; }
  .social li { width: 23px; height: 23px; border-radius: 50%; background: var(--social-grey); }
</style>
</head>
<body>
  <header class="site-header">
    <div class="brand">TEAMVORA</div>
    <span class="login-label email">Email</span>
    <div class="login-input email"></div>
    <span class="login-label password">Password</span>
    <div class="login-input password"></div>
    <div class="login-button">Login</div>
    <span class="login-note keep">
      <svg width="11" height="11" viewBox="0 0 11 11" aria-hidden="true"><rect x="0.5" y="0.5" width="10" height="10" fill="none" stroke="#fff"/><path d="M2.5 5.5 L4.5 7.5 L8.5 3" fill="none" stroke="#fff" stroke-width="1.6"/></svg>
      Keep me logged in
    </span>
    <span class="login-note forgot">Forgotten your password?</span>
  </header>

  <main class="hero">
    <div class="hero-photo" role="img" aria-label="Photo of a businessman on a white sofa talking on a phone while working on a laptop"></div>

    <section class="signup">
      <h1 class="signup-title">SIGN UP</h1>
      <p class="signup-tagline">It's free and always will be.</p>
      <div class="field first">First Name</div>
      <div class="field last">Sur Name</div>
      <div class="field wide email">E-mail</div>
      <div class="field wide email-again">Re enter E-mail</div>
      <div class="field wide password">Password</div>
      <div class="birthday-label">Birthday</div>
      <div class="select day">Day<svg width="9" height="5" viewBox="0 0 9 5"><path d="M0 0 H9 L4.5 5 Z" fill="#333"/></svg></div>
      <div class="select month">Month<svg width="9" height="5" viewBox="0 0 9 5"><path d="M0 0 H9 L4.5 5 Z" fill="#333"/></svg></div>
      <div class="select year">Year<svg width="9" height="5" viewBox="0 0 9 5"><path d="M0 0 H9 L4.5 5 Z" fill="#333"/></svg></div>
      <p class="terms">By clicking Sign Up, you agree to our Terms and that you have read our Data Policy, including our Cookie Use.</p>
      <div class="signup-button">Sign Up</div>
    </section>
  </main>

  <footer class="site-footer">
    <span class="copyright">Copyright© 2015. All Rights Reserved.</span>
    <ul class="social" aria-label="Social links">
      <li></li><li></li><li></li><li></li><li></li><li></li>
    </ul>
  </footer>
</body>
</html>
```